Brenlow Estates Website and Logo Design

We need a new logo and website designed for 'Brenlow Estates Ltd', which is a well established Guernsey property holding company founded in 1934.

The company does not currently have a website. The new website should be similar in style and layout to https://www.quorvanhall.example/.

Target Market(s)

Industry, Media, Tenants

Industry/Entity Type

Property Management

Logo Text

BEL OR Brenlow Estates Ltd OR BE

Coding

Coded - Design and coding required

Number of Pages Required

4 page

Font styles to use
Other font styles liked:
• Helvetica

Requirements
Must have
• The logo laying over the picture (like https://www.quorvanhall.example/).
• Big pictures on homepage (like https://www.quorvanhall.example/)

```html
<!DOCTYPE html>
<html lang="en">
<head>
<meta charset="utf-8">
<title>Brenlow Estates Ltd</title>
<link rel="stylesheet" href="https://fonts.googleapis.com/css2?family=Open+Sans:wght@400;600;700&family=Raleway:wght@300;400;600&family=Roboto+Condensed:wght@700&family=Roboto:wght@400;500;700&display=swap">
<style>
:root{
  --blue:#1e90ee;
  --blue-soft:#7ccaf7;
  --blue-band:#6fbff4;
  --black:#000;
  --white:#fff;
  --ink:#1a1a1a;
  --grey-text:#666;
  --news-grey:#7a7a7a;
  --follow-bg:#ececec;
}
*{box-sizing:border-box;margin:0;padding:0}
html,body{width:1200px;height:4523px;overflow:hidden;background:var(--white)}
body{font-family:"Open Sans",Arial,sans-serif;color:var(--ink)}
.page{position:relative;width:1200px;height:4523px;overflow:hidden}
.abs{position:absolute}
.photo{position:absolute;display:block}
.center{text-align:center}

/* hero */
.hero-photo{left:0;top:0;width:1200px;height:573px;background:linear-gradient(180deg,#9cc6e6 0%,#bcd6ea 30%,#7ea4c0 55%,#4c7694 80%,#2f5672 100%)}
.hero-band{left:0;top:573px;width:1200px;height:654px;background:var(--black)}
.brand-mark{left:90px;top:12px;width:200px;text-align:center}
.brand-mark .dot{width:100px;height:100px;border-radius:50%;border:5px solid var(--white);background:var(--blue);margin:0 auto}
.brand-mark .name{font-family:"Raleway",sans-serif;font-weight:600;color:var(--white);font-size:30px;line-height:34px;margin-top:10px}
.phone-box{left:859px;top:9px;width:262px;height:57px;display:flex}
.phone-box .ico{width:54px;height:57px;background:var(--black);display:flex;align-items:center;justify-content:center}
.phone-box .num{flex:1;background:var(--white);font-family:"Roboto",sans-serif;font-size:27px;display:flex;align-items:center;padding-left:12px;color:var(--ink)}
.menu{left:990px;top:66px;font-family:"Roboto",sans-serif;font-weight:700;color:var(--white);font-size:30px;display:flex;align-items:center;gap:12px;letter-spacing:1px}
.hero-title{left:0;top:187px;width:1200px;text-align:center}
.hero-title span{display:inline-block;background:var(--black);color:var(--white);font-family:"Roboto Condensed",sans-serif;font-weight:700;font-size:54px;line-height:72px;padding:0 20px;letter-spacing:1px}
.hero-sub{left:0;top:274px;width:1200px;text-align:center}
.hero-sub span{display:inline-block;background:var(--white);color:var(--ink);font-family:"Roboto",sans-serif;font-weight:700;font-size:30px;line-height:54px;padding:0 22px}
.btn-blue{background:var(--blue);color:var(--white);font-family:"Roboto",sans-serif;font-size:19px;text-transform:uppercase;display:flex;align-items:center;justify-content:center}
.contact-btn{left:500px;top:362px;width:202px;height:57px;border-radius:8px}
.thumb{top:516px;width:332px;height:235px;border:12px solid var(--white)}
.t1{left:78px;background:linear-gradient(160deg,#dfe7ee,#8aa7bf 55%,#2b3d52)}
.t2{left:440px;background:linear-gradient(160deg,#7e8fa0,#b8563a 45%,#5e5a55)}
.t3{left:793px;background:linear-gradient(180deg,#b9d3ea,#d7dde3 55%,#6c6f72)}

.welcome h2{font-family:"Raleway",sans-serif;font-weight:400;font-size:42px;color:var(--white)}
.welcome h2 em{font-style:normal;color:var(--blue)}
.welcome{left:81px;top:800px;width:620px}
.welcome p{color:var(--white);font-size:17.5px;line-height:36px;margin-top:20px}
.read-more-1{left:78px;top:1091px;width:166px;height:54px}
.side-mark{left:746px;top:848px;width:300px;text-align:center}
.side-mark .dot{width:104px;height:104px;border-radius:50%;border:5px solid var(--blue);margin:0 auto}
.side-mark .name{font-family:"Raleway",sans-serif;font-weight:600;color:var(--blue);font-size:44px;margin-top:18px;line-height:50px}

/* about */
.about-band{left:0;top:1227px;width:1200px;height:220px;background:linear-gradient(180deg,#5fb5f1,#8fd0f7)}
.about-photo{left:0;top:1447px;width:1200px;height:458px;background:linear-gradient(180deg,#b9c9d4 0%,#d6dde2 45%,#c2cbd1 75%,#e6e9eb 100%)}
.about-arrow{left:575px;top:1446px}
.about-text{left:0;top:1260px;width:1200px;text-align:center}
.about-text h2{font-family:"Raleway",sans-serif;font-weight:300;font-size:40px;color:var(--white)}
.about-text .lead{font-weight:700;font-size:20px;color:var(--ink);margin-top:10px}
.about-text .sub{font-size:18px;color:var(--white);line-height:27px;margin-top:6px}
.era{top:1492px;width:287px;text-align:center}
.era .circle{width:287px;height:287px;border-radius:50%;border:12px solid var(--blue)}
.era .label{font-family:"Roboto",sans-serif;font-weight:500;font-size:28px;margin-top:28px;color:var(--ink)}
.e1{left:81px}.e2{left:455px}.e3{left:830px}
.c1{background:linear-gradient(180deg,#a9c4dc,#7f9a6a 50%,#5d7e4c)}
.c2{background:linear-gradient(180deg,#4f7d55,#6a9bb0 50%,#b06b3c)}
.c3{background:linear-gradient(180deg,#9ec8ec,#c9a873 55%,#6a6e74)}

/* headings */
.sec-title{left:0;width:1200px;text-align:center;font-family:"Raleway",sans-serif;font-weight:400;font-size:40px;color:var(--ink)}
.sec-title em{font-style:normal;color:var(--blue)}

/* services */
.card{width:322px;text-align:center}
.card .img{height:217px}
.card h3{font-family:"Open Sans",sans-serif;font-weight:400;font-size:23px;color:var(--blue);margin-top:18px}
.card p{font-size:16px;line-height:19px;color:var(--grey-text);margin-top:6px;padding:0 24px}
.card .pill{width:154px;height:48px;border-radius:24px;margin:24px auto 0}
.s1{background:linear-gradient(180deg,#a9c8e6,#6d8faa 60%,#33546f)}
.s2{background:linear-gradient(180deg,#c3d6e8,#a99f92 50%,#4e6c86)}
.s3{background:linear-gradient(180deg,#9dc2e6,#8a9aa3 50%,#3e6b8c)}

/* testimonial */
.quote-band{left:0;top:2490px;width:1200px;height:290px;background:var(--blue-soft)}
.quote-icon{left:573px;top:2548px;width:54px;height:54px;border-radius:50%;border:2px solid var(--ink);display:flex;align-items:center;justify-content:center;font-family:"Roboto",sans-serif;font-size:28px}
.quote-text{left:150px;top:2616px;width:900px;text-align:center;font-size:17px;line-height:30px;color:var(--ink)}
.quote-name{left:0;top:2690px;width:1200px;text-align:center;font-size:20px}
.quote-name b{color:var(--ink)}
.quote-name span{color:var(--white)}

/* projects */
.proj{top:2909px;width:322px;text-align:center}
.proj .img{height:220px}
.proj h3{font-weight:400;font-size:22px;color:var(--grey-text);margin-top:22px}
.proj p{font-size:16.5px;line-height:19px;color:var(--ink);margin-top:4px;padding:0 20px}
.p1{background:linear-gradient(170deg,#b8b1a8,#8a4a3c 50%,#5d5955)}
.p2{background:linear-gradient(170deg,#d7d3cd,#7b7f86 50%,#3d3f44)}
.p3{background:linear-gradient(180deg,#2f5aa8,#7ea7cf 50%,#a99883)}
.view-all{left:510px;top:3247px;width:181px;height:57px;border:6px solid var(--blue);display:flex;align-items:center;justify-content:center;font-family:"Roboto",sans-serif;font-size:23px;color:var(--ink);text-transform:uppercase}

/* news */
.news-band{left:0;top:3353px;width:1200px;height:702px;background:var(--news-grey)}
.news-title{color:var(--white)}
.news-title em{color:var(--white)}
.news{top:3479px;width:501px;text-align:center}
.news .img{height:314px;position:relative}
.news .date{position:absolute;left:0;top:0;width:66px;height:66px;background:var(--black);color:var(--white);text-align:center;font-family:"Roboto",sans-serif}
.news .date b{display:block;font-size:30px;font-weight:400;line-height:40px}
.news .date small{font-size:13px}
.news h3{font-size:17px;font-weight:700;color:var(--black);margin-top:34px}
.news p{font-size:16px;line-height:19px;color:var(--black);margin-top:10px;padding:0 60px}
.n1{left:78px}.n2{left:621px}
.ni1{background:linear-gradient(180deg,#6a9ec7,#c3c7b3 60%,#d8a85c)}
.ni2{background:linear-gradient(180deg,#6f7f96,#c9a184 45%,#3d5f82)}
.read-more-2{left:513px;top:3941px;width:178px;height:57px;background:var(--white);border:6px solid var(--black);display:flex;align-items:center;justify-content:center;font-family:"Roboto",sans-serif;font-size:23px;color:var(--ink);text-transform:uppercase}

/* follow */
.follow{left:0;top:4055px;width:1200px;height:82px;background:var(--follow-bg);display:flex;align-items:center;padding-left:81px;font-size:16px}
.follow h4{font-family:"Raleway",sans-serif;font-weight:400;color:var(--blue);font-size:29px;width:172px}
.follow .item{display:flex;align-items:center;gap:12px;width:292px}
.follow .sq{width:44px;height:44px;background:var(--white)}
.follow .sq i{display:block;width:100%;height:100%}

/* footer */
.footer{left:0;top:4137px;width:1200px;height:259px;background:var(--black);color:var(--white)}
.nav{position:absolute;top:51px;left:78px;font-size:20px;font-family:"Roboto",sans-serif}
.nav a{position:absolute;color:var(--white);text-decoration:none;white-space:nowrap}
.social{position:absolute;top:42px;width:50px;height:50px;border-radius:50%;background:var(--white)}
.social.first{background:var(--blue)}
.rule{position:absolute;left:78px;top:132px;width:1044px;height:1px;background:#555}
.contact{position:absolute;top:158px;display:flex;align-items:center;gap:14px;font-size:16px;line-height:21px}
.contact .dot{width:46px;height:46px;border-radius:50%;background:var(--white);display:flex;align-items:center;justify-content:center;flex:none}
.subscribe-bar{left:0;top:4396px;width:1200px;height:127px;background:var(--blue)}
.email{position:absolute;left:78px;top:33px;width:612px;height:60px;border-radius:30px;background:var(--white);display:flex;align-items:center;padding-left:30px;gap:14px;font-size:20px;color:var(--ink)}
.email .go{position:absolute;right:4px;top:4px;width:180px;height:52px;border-radius:26px;background:var(--black);color:var(--white);display:flex;align-items:center;justify-content:center;font-family:"Roboto",sans-serif;font-size:19px;text-transform:uppercase}
.copy{position:absolute;left:905px;top:40px;color:var(--white);font-size:15px;line-height:24px}
.copy b{font-family:"Roboto",sans-serif}
</style>
</head>
<body>
<div class="page">

  <!-- hero -->
  <div class="photo hero-photo" role="img" aria-label="Harbour with moored boats and waterfront town houses under a blue sky"></div>
  <div class="abs hero-band"></div>

  <div class="abs brand-mark">
    <div class="dot"></div>
    <div class="name">Brenlow Estates</div>
  </div>

  <div class="abs phone-box">
    <div class="ico">
      <svg width="28" height="28" viewBox="0 0 24 24"><path fill="#fff" d="M6.6 10.8a15 15 0 0 0 6.6 6.6l2.2-2.2c.3-.3.7-.4 1-.2 1.1.4 2.3.6 3.6.6.6 0 1 .4 1 1V20c0 .6-.4 1-1 1A17 17 0 0 1 3 4c0-.6.4-1 1-1h3.5c.6 0 1 .4 1 1 0 1.3.2 2.5.6 3.6.1.3 0 .7-.2 1z"/></svg>
    </div>
    <div class="num">555-014-2273</div>
  </div>
  <div class="abs menu">MENU
    <svg width="30" height="26" viewBox="0 0 30 26"><rect y="1" width="30" height="5" fill="#fff"/><rect y="11" width="30" height="5" fill="#fff"/><rect y="21" width="30" height="5" fill="#fff"/></svg>
  </div>

  <div class="abs hero-title"><span>BRENLOW</span></div>
  <div class="abs hero-sub"><span>Estates Business Ltd</span></div>
  <div class="abs btn-blue contact-btn">Contact Now</div>

  <div class="photo thumb t1" role="img" aria-label="Hovercraft crossing the water"></div>
  <div class="photo thumb t2" role="img" aria-label="Group climbing coastal rocks in safety gear"></div>
  <div class="photo thumb t3" role="img" aria-label="Helicopter parked on a landing pad"></div>

  <div class="abs welcome">
    <h2>Welcome to <em>Brenlow Estates</em></h2>
    <p>Brenlow Estates Limited (BEL) is a family-owned Guernsey property holding company. It purchases properties that are considered to have potential for development either through refurbishment or by obtaining planning permission to change its classification from, for example, industrial premises to offices or retail outlets, or by the marriage value of buying an adjacent property to one already owned by BEL.</p>
  </div>
  <div class="abs btn-blue read-more-1">Read More</div>
  <div class="abs side-mark">
    <div class="dot"></div>
    <div class="name">Brenlow Estates</div>
  </div>

  <!-- about -->
  <div class="abs about-band"></div>
  <div class="photo about-photo" role="img" aria-label="Misty coastal beach scene in soft grey blue tones"></div>
  <svg class="abs about-arrow" width="50" height="26" viewBox="0 0 50 26"><polygon points="0,0 50,0 25,26" fill="#8fd0f7"/></svg>
  <div class="abs about-text">
    <h2>About Brenlow Estates</h2>
    <p class="lead">Lorem Ipsum is simply dummy text of the printing and typesetting industry.</p>
    <p class="sub">Lorem Ipsum is simply dummy text of the printing and typesetting industry. Lorem Ipsum has been the<br>industry's standard dummy text ever since the 1500s.</p>
  </div>
  <div class="abs era e1"><div class="circle c1" role="img" aria-label="Aerial view of green island fields"></div><div class="label">YESTERDAY</div></div>
  <div class="abs era e2"><div class="circle c2" role="img" aria-label="Small boats moored at a wooden jetty"></div><div class="label">TODAY</div></div>
  <div class="abs era e3"><div class="circle c3" role="img" aria-label="Harbour town houses along the waterfront"></div><div class="label">TOMORROW</div></div>

  <!-- services -->
  <h2 class="abs sec-title" style="top:1960px">Brenlow Estates <em>Services</em></h2>
  <div class="abs card" style="left:78px;top:2050px">
    <div class="img s1" role="img" aria-label="Bay with sailing boats and island rocks"></div>
    <h3>Lorem Ipsum</h3>
    <p>Lorem Ipsum is simply dummy text of the printing and typesetting industry.</p>
    <div class="btn-blue pill">Read More</div>
  </div>
  <div class="abs card" style="left:440px;top:2050px">
    <div class="img s2" role="img" aria-label="Town skyline above a busy marina"></div>
    <h3>Lorem Ipsum</h3>
    <p>Lorem Ipsum is simply dummy text of the printing and typesetting industry.</p>
    <div class="btn-blue pill">Read More</div>
  </div>
  <div class="abs card" style="left:802px;top:2050px">
    <div class="img s3" role="img" aria-label="Harbour wall and boats in calm water"></div>
    <h3>Lorem Ipsum</h3>
    <p>Lorem Ipsum is simply dummy text of the printing and typesetting industry.</p>
    <div class="btn-blue pill">Read More</div>
  </div>

  <!-- testimonial -->
  <div class="abs quote-band"></div>
  <div class="abs quote-icon">«</div>
  <p class="abs quote-text">Lorem Ipsum is simply dummy text of the printing and typesetting industry. Lorem Ipsum has been the industry's standard dummy text ever since the 1500s, when an unknown printer took a galley.</p>
  <p class="abs quote-name"><b>NELA HARTWICK,</b> <span>Head Officer at Pellrow Company</span></p>

  <!-- projects -->
  <h2 class="abs sec-title" style="top:2836px">Current <em>Projects</em></h2>
  <div class="abs proj" style="left:78px">
    <div class="img p1" role="img" aria-label="Team in helmets on a rocky outcrop"></div>
    <h3>Project Title</h3>
    <p>Lorem Ipsum is simply dummy text of the printing and typesetting industry.</p>
  </div>
  <div class="abs proj" style="left:440px">
    <div class="img p2" role="img" aria-label="Business meeting reviewing documents"></div>
    <h3>Project Title</h3>
    <p>Lorem Ipsum is simply dummy text of the printing and typesetting industry.</p>
  </div>
  <div class="abs proj" style="left:802px">
    <div class="img p3" role="img" aria-label="Beach at low tide with small boats"></div>
    <h3>Project Title</h3>
    <p>Lorem Ipsum is simply dummy text of the printing and typesetting industry.</p>
  </div>
  <div class="abs view-all">View All</div>

  <!-- news -->
  <div class="abs news-band"></div>
  <h2 class="abs sec-title news-title" style="top:3400px">Latest <em>News</em></h2>
  <div class="abs news n1">
    <div class="img ni1" role="img" aria-label="Paraglider over the coast at sunset"><div class="date"><b>14</b><small>MAY</small></div></div>
    <h3>Lorem Ipsum is simply text Dummy</h3>
    <p>Lorem Ipsum is simply dummy text of the printing and typesetting industry.</p>
  </div>
  <div class="abs news n2">
    <div class="img ni2" role="img" aria-label="Marina full of yachts at dusk"><div class="date"><b>26</b><small>JAN</small></div></div>
    <h3>Lorem Ipsum is simply text Dummy</h3>
    <p>Lorem Ipsum is simply dummy text of the printing and typesetting industry.</p>
  </div>
  <div class="abs read-more-2">Read More</div>

  <!-- follow -->
  <div class="abs follow">
    <h4>Follow Us</h4>
    <div class="item"><span class="sq"></span>tweet@orvelmedia.example</div>
    <div class="item"><span class="sq"></span>Watch Our Latest Vedio</div>
    <div class="item"><span class="sq"></span>Subscribe Our News</div>
  </div>

  <!-- footer -->
  <div class="abs footer">
    <nav class="nav">
      <a style="left:0">Home</a>
      <a style="left:103px">About</a>
      <a style="left:208px">Services</a>
      <a style="left:341px">Projects</a>
      <a style="left:462px">News</a>
      <a style="left:561px">Contact</a>
    </nav>
    <span class="social first" style="left:888px"></span>
    <span class="social" style="left:946px"></span>
    <span class="social" style="left:1006px"></span>
    <span class="social" style="left:1066px"></span>
    <div class="rule"></div>
    <div class="contact" style="left:78px;width:330px">
      <span class="dot"><svg width="20" height="24" viewBox="0 0 20 24"><path fill="#000" d="M10 0a8 8 0 0 0-8 8c0 6 8 16 8 16s8-10 8-16a8 8 0 0 0-8-8zm0 11a3 3 0 1 1 0-6 3 3 0 0 1 0 6z"/></svg></span>
      <span>Lorem Ipsum is simply dummy text<br>of the printing.</span>
    </div>
    <div class="contact" style="left:505px">
      <span class="dot"><svg width="22" height="22" viewBox="0 0 24 24"><path fill="#000" d="M6.6 10.8a15 15 0 0 0 6.6 6.6l2.2-2.2c.3-.3.7-.4 1-.2 1.1.4 2.3.6 3.6.6.6 0 1 .4 1 1V20c0 .6-.4 1-1 1A17 17 0 0 1 3 4c0-.6.4-1 1-1h3.5c.6 0 1 .4 1 1 0 1.3.2 2.5.6 3.6.1.3 0 .7-.2 1z"/></svg></span>
      <span>555-018-3390</span>
    </div>
    <div class="contact" style="left:824px">
      <span class="dot"><svg width="22" height="16" viewBox="0 0 22 16"><rect x="1" y="1" width="20" height="14" fill="none" stroke="#000" stroke-width="2"/><path d="M1 1l10 8 10-8" fill="none" stroke="#000" stroke-width="2"/></svg></span>
      <span>hello@brenlowestates.example</span>
    </div>
  </div>

  <div class="abs subscribe-bar">
    <div class="email">
      <svg width="24" height="18" viewBox="0 0 22 16"><rect x="1" y="1" width="20" height="14" fill="none" stroke="#1a1a1a" stroke-width="2"/><path d="M1 1l10 8 10-8" fill="none" stroke="#1a1a1a" stroke-width="2"/></svg>
      Email
      <span class="go">Subscribe!</span>
    </div>
    <p class="copy">©&nbsp; <b>BRENLOW ESTATES</b><br>&nbsp;&nbsp;&nbsp;&nbsp; 2016. All Rights Reserveds</p>
  </div>

</div>
</body>
</html>
```